KELBRIDGE PAINTING

We are a painting company. We paint residential, commercial and strata jobs. I need the website to be very sharp, neat and elegant. I've attached our logo. the Logo needs to be embossed as a gold color and the background like a Matt black. I need these tabs:

• HOME • ABOUT US • SERVICES • TESTIMONIALS • SHOWCASE • CONTACT US

Be creative and innovative in your style.
take this as an example to just get the gist of what I'm expecting. If you can better it then the job is yours!

http://rickhalvorpainting.com.au/contact.html

I look forward to seeing your artwork :)

#These are the links to my logo in PSD format.

https://www.filevaultzy.com/s/qwertplk83nd7ha/Kelbridge%20Painting%20Luxury%20Gold.rar

https://www.filevaultzy.com/sh/bzuyrak2m5wqp9/QoPL7-xvMn

Painting

• Making the Logo embossed like the artworks i have attached is definitely a necessity.

Can you let me know if this is possible to apply to the website.

thank you

```html
<!DOCTYPE html>
<html lang="en">
<head>
<meta charset="utf-8">
<title>Kelbridge Painting – Contact us</title>
<link href="https://fonts.googleapis.com/css2?family=Source+Sans+3:ital,wght@0,400;0,600;0,700;1,400&display=swap" rel="stylesheet">
<style>
:root{
  --ink:#1e222b;
  --gold:#f3c14a;
  --gold-deep:#d6a419;
  --gold-pale:#f2d9a0;
  --field:#6d7277;
  --field-active:#9a9ca1;
  --steel:#4e5359;
  --steel-light:#8e9297;
  --footer:#9b9fa5;
  --white:#ffffff;
  --line:#3e434c;
}
*{box-sizing:border-box;margin:0;padding:0}
html,body{width:946px;height:1200px;overflow:hidden}
body{background:var(--ink);font-family:"Source Sans 3",sans-serif;color:var(--white);position:relative}
.abs{position:absolute}
.header{left:0;top:0;width:946px;height:73px;background:var(--ink);border-bottom:1px solid #8a7a4a}
.phone-top{left:684px;top:14px;font-size:19px;font-weight:700;color:var(--gold);display:flex;align-items:center;gap:7px}
.nav{right:130px;top:50px;display:flex;gap:24px;font-size:12px;font-weight:600;letter-spacing:.3px}
.nav a{color:var(--white);text-decoration:none}
.nav a.current{color:var(--gold)}
.hero{left:0;top:74px;width:946px;height:356px;background:linear-gradient(180deg,#5b4232 0%,#7a5c45 45%,#a38a78 75%,#b9a597 100%)}
.brand-band{left:184px;top:74px;width:435px;height:30px;background:linear-gradient(90deg,#f6cc55,#e9b93a 60%,#f0cf6e);display:flex;align-items:center;padding-left:48px;color:#1e222b}
.brand-name{font-size:17px;font-weight:700;letter-spacing:.6px}
.brand-sep{width:1px;height:16px;background:#1e222b;margin:0 12px}
.brand-tag{font-size:14px;font-style:italic}
.logo-ring{left:131px;top:15px;width:94px;height:94px;border-radius:50%;background:var(--ink)}
.logo-mark{left:143px;top:24px;width:72px;height:72px;border-radius:50%;border:3px solid var(--gold)}
.slide-dots{left:764px;top:98px;display:flex;gap:6px}
.slide-dots span{width:7px;height:7px;background:#2e323a}
.slide-dots span.on{background:var(--gold)}
.caption-accent-a{left:131px;top:264px;width:44px;height:44px;background:var(--gold-deep)}
.caption-accent-b{left:524px;top:309px;width:131px;height:80px;background:var(--gold-deep)}
.caption-tick{left:613px;top:272px;width:28px;height:5px;background:#8e9297}
.caption{left:139px;top:272px;width:502px;height:109px;background:var(--ink);padding:14px 0 0 28px;font-size:34px;line-height:39px}
.stripe{height:7px;display:flex}
.stripe span{display:block;height:100%}
.page-title{left:130px;top:466px;font-size:36px;font-weight:700;color:var(--gold)}
.lead{left:130px;top:528px;font-size:13.5px}
.label{left:130px;font-size:11.5px;font-weight:600}
.field{left:131px;width:218px;height:28px;background:var(--field);border:1px solid #7c8085}
.field.active{background:var(--field-active);border:2px solid var(--gold-deep)}
.btn{top:974px;height:28px;font-size:11.5px;font-weight:700;display:flex;align-items:center;justify-content:center}
.btn-submit{left:131px;width:69px;background:var(--gold-deep);color:var(--ink)}
.btn-reset{left:211px;width:70px;background:var(--steel);color:#d8dadd}
.details-title{left:618px;top:474px;font-size:23px;font-weight:700;color:var(--gold)}
.details-row{left:618px;width:197px;border-top:1px solid var(--line);display:flex}
.details-row .icon{width:26px;display:flex;justify-content:center;padding-top:9px;border-right:1px solid var(--line)}
.details-row .text{padding:8px 0 0 11px;font-size:11.5px;line-height:14.5px}
.footer{left:0;top:1069px;width:946px;height:131px;background:var(--footer);color:#2b2f36}
.brands-label{left:132px;top:22px;font-size:17px;line-height:15px;font-weight:600}
.brands-label small{display:block;font-size:12px;font-weight:700}
.partner{top:24px;font-size:20px;font-weight:700;color:#2b3566;display:flex;align-items:center;gap:6px}
.partner i{display:inline-block;width:12px;height:12px}
.copyright{left:132px;top:99px;font-size:10.5px}
.social{top:93px;width:24px;height:24px;border-radius:50%;background:#3b3f47}
</style>
</head>
<body>

<header class="abs header"></header>
<div class="abs phone-top">
  <svg width="16" height="16" viewBox="0 0 24 24"><path fill="#f3c14a" d="M6.6 10.8c1.4 2.8 3.8 5.1 6.6 6.6l2.2-2.2c.3-.3.7-.4 1-.2 1.1.4 2.3.6 3.6.6.6 0 1 .4 1 1V20c0 .6-.4 1-1 1C10.6 21 3 13.4 3 4c0-.6.4-1 1-1h3.5c.6 0 1 .4 1 1 0 1.3.2 2.5.6 3.6.1.3 0 .7-.2 1z"/></svg>
  1300 47 19 62
</div>
<nav class="abs nav">
  <a href="#">HOME</a><a href="#">ABOUT US</a><a href="#">SERVICES</a><a href="#">TESTIMONIALS</a><a href="#">SHOWCASE</a><a href="#" class="current">CONTACT US</a>
</nav>

<div class="abs hero" role="img" aria-label="Photo of a modern living room with a brown and cream curved leather sofa"></div>
<div class="abs brand-band">
  <span class="brand-name">KELBRIDGE PAINTING</span><span class="brand-sep"></span><span class="brand-tag">Painting Australia Everyday!</span>
</div>
<div class="abs logo-ring"></div>
<div class="abs logo-mark" aria-label="Kelbridge Painting"></div>
<div class="abs slide-dots"><span></span><span></span><span></span><span class="on"></span></div>

<div class="abs caption-accent-a"></div>
<div class="abs caption-accent-b"></div>
<div class="abs caption-tick"></div>
<div class="abs caption">We paint residential,<br>commercial and strata jobs</div>

<div class="abs stripe" style="left:0;top:430px;width:946px">
  <span style="width:227px;background:transparent"></span>
  <span style="width:64px;background:#4e5359"></span>
  <span style="width:72px;background:#6d7277"></span>
  <span style="width:111px;background:#8e9297"></span>
  <span style="width:95px;background:var(--gold-deep)"></span>
  <span style="width:64px;background:#e7b63c"></span>
  <span style="width:71px;background:#efc878"></span>
  <span style="width:242px;background:var(--gold-pale)"></span>
</div>

<h1 class="abs page-title">Contact us</h1>
<p class="abs lead">For a FREE quote, send us a message:</p>

<div class="abs label" style="top:574px">NAME *</div>
<div class="abs field active" style="top:593px"></div>
<div class="abs label" style="top:632px">EMAIL *</div>
<div class="abs field" style="top:651px"></div>
<div class="abs label" style="top:690px">PHONE *</div>
<div class="abs field" style="top:709px"></div>
<div class="abs label" style="top:748px;left:133px">SUBURB OR POSTCODE *</div>
<div class="abs field" style="top:767px"></div>
<div class="abs label" style="top:806px">DETAILS *</div>
<div class="abs field" style="top:826px;width:334px;height:132px"></div>
<div class="abs btn btn-submit">SUBMIT</div>
<div class="abs btn btn-reset">RESET</div>

<h2 class="abs details-title">Details</h2>
<div class="abs details-row" style="top:511px;height:73px">
  <div class="icon"><svg width="16" height="16" viewBox="0 0 16 16"><path fill="#8e9297" d="M7 1h2v14H7zM2 3h12l-2 2H2zM3 7h10v2H5z"/></svg></div>
  <div class="text">Lorem ipsum dolor sit amet consectetur adipiscing elit Quantum Aristoxeni ingenium consumptum.</div>
</div>
<div class="abs details-row" style="top:584px;height:38px">
  <div class="icon"><svg width="14" height="14" viewBox="0 0 24 24"><path fill="#8e9297" d="M6.6 10.8c1.4 2.8 3.8 5.1 6.6 6.6l2.2-2.2c.3-.3.7-.4 1-.2 1.1.4 2.3.6 3.6.6.6 0 1 .4 1 1V20c0 .6-.4 1-1 1C10.6 21 3 13.4 3 4c0-.6.4-1 1-1h3.5c.6 0 1 .4 1 1 0 1.3.2 2.5.6 3.6.1.3 0 .7-.2 1z"/></svg></div>
  <div class="text" style="font-size:17px;font-weight:600;padding-top:7px">1300 47 19 62</div>
</div>
<div class="abs details-row" style="top:622px;height:35px">
  <div class="icon"><svg width="16" height="12" viewBox="0 0 16 12"><rect x="0.5" y="0.5" width="15" height="11" fill="#8e9297"/><path d="M1 1l7 6 7-6M1 11l5-5M15 11l-5-5" stroke="#1e222b" fill="none"/></svg></div>
  <div class="text" style="padding-top:10px">mail@kelbridgepainting.com.au</div>
</div>

<div class="abs stripe" style="left:0;top:1062px;width:946px">
  <span style="width:241px;background:var(--gold-pale)"></span>
  <span style="width:72px;background:#efc878"></span>
  <span style="width:64px;background:#e7b63c"></span>
  <span style="width:96px;background:var(--gold-deep)"></span>
  <span style="width:111px;background:#8e9297"></span>
  <span style="width:71px;background:#6d7277"></span>
  <span style="width:65px;background:#4e5359"></span>
</div>

<footer class="abs footer">
  <div class="abs brands-label">BRANDS<small>USED BY US</small></div>
  <div class="abs partner" style="left:250px"><i style="background:#2b3566"></i>Corvane</div>
  <div class="abs partner" style="left:374px">Brelmix</div>
  <div class="abs partner" style="left:496px"><i style="background:#2b2f36;border-radius:50%"></i>Halverin</div>
  <div class="abs partner" style="left:674px">Durasheen</div>
  <p class="abs copyright">Copyright @ 2013 Kelbridge Painting. All rights reserved.</p>
  <div class="abs social" style="left:681px;background:#4a6ea8" aria-label="Social link"></div>
  <div class="abs social" style="left:717px" aria-label="Social link"></div>
  <div class="abs social" style="left:753px" aria-label="Social link"></div>
  <div class="abs social" style="left:790px" aria-label="Social link"></div>
</footer>

</body>
</html>
```